Business Card for a Jewellery Brand

Business card for an upscale jewellery brand. Attached is the brand logo and icon and color board. I am looking for two card versions: one for the founder and one is generic. The card should be elegant and convey upscale and premium feel. I am open to both square and rectangle card shapes.

Industry/Entity Type

Jewelry

Contact Information for Business Card

Two cards: (1) Sunela Parvaniya (Founder) (2) General
(1) Sunela Parvaniya card should have Name: Sunela Parvaniya, Title: Founder Email id: sunela@quiremo.com.au. Phone no: +61452913307
(2) Generic card should have Email id: info@quiremo.com.au. Phone no: +61436207518

Requirements
Must have
• Workmark
• ICON
• Phone no
• Email ID
• ABN: 58219740312 (Note: ABN is Business number in Australia)
• Website: www.quiremo.com.au
• Instagram: quiremo_jewellery
• Facebook: @quiremojewellery
Nice to have
• Tagline

```html
<!DOCTYPE html>
<html lang="en">
<head>
<meta charset="utf-8">
<title>Quiremo Business Cards</title>
<link href="https://fonts.googleapis.com/css2?family=Roboto:wght@400;500&family=Roboto+Condensed:wght@500&display=swap" rel="stylesheet">
<style>
  :root {
    --backdrop: #3a302b;
    --card: #232325;
    --card-pattern: #2b2b2e;
    --rose: #e79a8c;
    --rose-deep: #a66b62;
    --ink-light: #e8e4e2;
    --ink-muted: #bdb7b4;
  }
  * { margin: 0; padding: 0; box-sizing: border-box; }
  html, body {
    width: 1200px;
    height: 769px;
    overflow: hidden;
    background: var(--backdrop);
    font-family: "Roboto", sans-serif;
  }
  .stage {
    width: 1200px;
    height: 769px;
    display: flex;
    align-items: center;
    justify-content: center;
    gap: 60px;
  }
  .card {
    position: relative;
    width: 510px;
    height: 292px;
    background: var(--card);
    border-radius: 3px;
    overflow: hidden;
    box-shadow: 0 18px 40px rgba(0, 0, 0, 0.45);
  }
  .card-texture {
    position: absolute;
    inset: 0;
    background: radial-gradient(circle at 50% 40%, var(--card-pattern), var(--card) 75%);
  }
  .card-content {
    position: relative;
    height: 100%;
    padding: 0 20px;
    display: flex;
    flex-direction: column;
    align-items: center;
    justify-content: center;
    text-align: center;
  }
  .wordmark {
    color: var(--rose);
    font-weight: 500;
    letter-spacing: 0.28em;
    display: flex;
    align-items: center;
    gap: 10px;
    white-space: nowrap;
  }
  .wordmark-dot {
    width: 10px;
    height: 10px;
    border-radius: 50%;
    background: var(--rose);
  }
  .founder .wordmark { font-size: 17px; margin-bottom: 18px; }
  .person-name {
    color: var(--rose);
    font-family: "Roboto Condensed", sans-serif;
    font-weight: 500;
    font-size: 21px;
    letter-spacing: 0.04em;
    text-transform: uppercase;
  }
  .person-title {
    color: var(--ink-muted);
    font-size: 14px;
    margin-top: 3px;
    margin-bottom: 14px;
  }
  .contact-row {
    display: flex;
    align-items: center;
    justify-content: center;
    gap: 12px;
    color: var(--ink-light);
    font-size: 13px;
    line-height: 1;
    margin-bottom: 8px;
    white-space: nowrap;
  }
  .contact-item { display: flex; align-items: center; gap: 5px; }
  .contact-icon { width: 12px; height: 12px; flex: none; }
  .social-mark {
    width: 10px;
    height: 10px;
    background: var(--rose);
    border-radius: 2px;
    flex: none;
  }
  .abn {
    color: var(--ink-light);
    font-size: 13px;
    margin-top: 6px;
  }
  .general .wordmark {
    font-size: 40px;
    color: var(--rose-deep);
    letter-spacing: 0.3em;
    margin-bottom: 30px;
    padding-left: 0.3em;
  }
</style>
</head>
<body>
<main class="stage">
  <section class="card founder">
    <div class="card-texture" role="img" aria-label="Subtle tonal floral lattice pattern across the card face"></div>
    <div class="card-content">
      <div class="wordmark"><span class="wordmark-dot"></span>QUIREMO</div>
      <h1 class="person-name">Sunela Parvaniya</h1>
      <p class="person-title">Founder</p>
      <div class="contact-row">
        <span class="contact-item">
          <svg class="contact-icon" viewBox="0 0 12 12" aria-hidden="true"><rect x="3" y="0.8" width="6" height="10.4" rx="1" fill="none" stroke="var(--rose)" stroke-width="1.2"/><circle cx="6" cy="9.3" r="0.6" fill="var(--rose)"/></svg>
          +61452913307
        </span>
        <span class="contact-item">
          <svg class="contact-icon" viewBox="0 0 12 12" aria-hidden="true"><rect x="0.5" y="2.5" width="11" height="7" fill="var(--rose)"/><path d="M0.5 2.5 L6 6.5 L11.5 2.5" fill="none" stroke="var(--card)" stroke-width="1"/></svg>
          sunela@quiremo.com.au
        </span>
      </div>
      <div class="contact-row">
        <span class="contact-item">
          <svg class="contact-icon" viewBox="0 0 12 12" aria-hidden="true"><circle cx="6" cy="6" r="5.5" fill="var(--rose)"/><path d="M0.8 6 H11.2 M6 0.6 C3.6 3 3.6 9 6 11.4 M6 0.6 C8.4 3 8.4 9 6 11.4" fill="none" stroke="var(--card)" stroke-width="0.8"/></svg>
          www.quiremo.com.au
        </span>
        <span class="contact-item"><span class="social-mark"></span>quiremo_jewellery</span>
        <span class="contact-item"><span class="social-mark"></span>@quiremojewellery</span>
      </div>
      <p class="abn">ABN:58219740312</p>
    </div>
  </section>

  <section class="card general">
    <div class="card-texture" role="img" aria-label="Subtle tonal floral lattice pattern across the card face"></div>
    <div class="card-content">
      <div class="wordmark">QUIREMO</div>
      <div class="contact-row">
        <span class="contact-item">
          <svg class="contact-icon" viewBox="0 0 12 12" aria-hidden="true"><rect x="3" y="0.8" width="6" height="10.4" rx="1" fill="none" stroke="var(--rose)" stroke-width="1.2"/><circle cx="6" cy="9.3" r="0.6" fill="var(--rose)"/></svg>
          +61436207518
        </span>
        <span class="contact-item">
          <svg class="contact-icon" viewBox="0 0 12 12" aria-hidden="true"><rect x="0.5" y="2.5" width="11" height="7" fill="var(--rose)"/><path d="M0.5 2.5 L6 6.5 L11.5 2.5" fill="none" stroke="var(--card)" stroke-width="1"/></svg>
          info@quiremo.com.au
        </span>
      </div>
      <div class="contact-row">
        <span class="contact-item">
          <svg class="contact-icon" viewBox="0 0 12 12" aria-hidden="true"><circle cx="6" cy="6" r="5.5" fill="var(--rose)"/><path d="M0.8 6 H11.2 M6 0.6 C3.6 3 3.6 9 6 11.4 M6 0.6 C8.4 3 8.4 9 6 11.4" fill="none" stroke="var(--card)" stroke-width="0.8"/></svg>
          www.quiremo.com.au
        </span>
        <span class="contact-item"><span class="social-mark"></span>quiremo_jewellery</span>
        <span class="contact-item"><span class="social-mark"></span>@quiremojewellery</span>
      </div>
      <p class="abn">ABN:58219740312</p>
    </div>
  </section>
</main>
</body>
</html>
```